IT Company requires new Business Card design.

Over the years we have had a few different business card designs. We are now due for new cards across the board for all staff. We felt this would be a good time to start fresh with a new design. Our traditional card simply had our details on the front, and a list of services on the back. We don't particularly need the list of services, we have had cards where the only thing on the rear of the card was our logo.
Feel free to be creative, we would like our tag line "Complete IT Management" to appear at some point, doesn't necessarily have to be with the logo.
I have attached samples and drafts of various previous cards we have used over the years.

```html
<!DOCTYPE html>
<html lang="en">
<head>
<meta charset="utf-8">
<title>Ridgeway Systems – Business Card</title>
<link rel="stylesheet" href="https://fonts.googleapis.com/css2?family=Open+Sans:wght@400;600;800&display=swap">
<style>
  :root {
    --slate: #5e6f7c;
    --slate-dark: #4a5965;
    --ink: #2f3338;
    --card: #ffffff;
    --stage: #e6e6ea;
  }
  * { box-sizing: border-box; margin: 0; padding: 0; }
  html, body { width: 1200px; height: 987px; overflow: hidden; }
  body {
    background: var(--stage);
    font-family: "Open Sans", Arial, sans-serif;
    color: var(--ink);
    position: relative;
  }
  .card {
    position: absolute;
    left: 220px;
    width: 760px;
    height: 463px;
    background: var(--card);
    border-radius: 28px;
    overflow: hidden;
    box-shadow: 0 6px 18px rgba(0,0,0,0.12);
  }
  .card--back { top: 14px; }
  .card--front { top: 505px; }

  /* Back */
  .brand-back {
    position: absolute;
    left: 0; right: 0; top: 150px;
    display: flex; align-items: center; justify-content: center; gap: 18px;
  }
  .brand-mark {
    width: 70px; height: 70px;
    background: var(--slate);
  }
  .brand-name {
    color: var(--slate);
    font-weight: 800;
    text-transform: uppercase;
    line-height: 0.95;
  }
  .brand-back .brand-name { font-size: 52px; }
  .web-back {
    position: absolute; left: 0; right: 0; top: 300px;
    text-align: center;
    font-size: 22px; letter-spacing: 1.5px;
    color: var(--ink);
  }

  /* Front */
  .brand-front {
    position: absolute; left: 50px; top: 70px;
  }
  .brand-front .brand-row { display: flex; align-items: center; gap: 14px; }
  .brand-front .brand-mark { width: 50px; height: 50px; }
  .brand-front .brand-name { font-size: 36px; }
  .tagline {
    margin-top: 8px; margin-left: 64px;
    font-size: 11px; letter-spacing: 3.2px;
    color: var(--slate); text-transform: uppercase;
  }
  .divider {
    position: absolute; left: 380px; top: 60px;
    width: 1px; height: 190px;
    background: linear-gradient(var(--slate), rgba(94,111,124,0));
  }
  .person { position: absolute; left: 405px; top: 62px; }
  .person-name { font-size: 25px; font-weight: 800; color: var(--slate); }
  .person-role { font-size: 21px; color: var(--ink); margin-top: -2px; }
  .contacts { list-style: none; margin-top: 14px; }
  .contacts li {
    display: flex; align-items: center; gap: 10px;
    font-size: 20px; line-height: 29px; color: var(--ink);
  }
  .contacts svg { width: 16px; height: 16px; fill: var(--slate-dark); flex: none; }

  .swoosh { position: absolute; left: 0; bottom: 0; width: 760px; height: 463px; }
  .address {
    position: absolute; left: 60px; bottom: 34px;
    color: #fff; font-size: 22px; line-height: 30px;
  }
</style>
</head>
<body>

<section class="card card--back" aria-label="Card back">
  <div class="brand-back">
    <span class="brand-mark"></span>
    <span class="brand-name">Ridgeway<br>Systems</span>
  </div>
  <p class="web-back">www.ridgewaysystems.com.au</p>
</section>

<section class="card card--front" aria-label="Card front">
  <svg class="swoosh" viewBox="0 0 760 463" aria-hidden="true">
    <path d="M0 255 C 120 300, 260 330, 420 370 C 560 405, 680 430, 760 463 L 0 463 Z" fill="var(--slate)"/>
    <path d="M0 240 C 130 285, 270 318, 430 356 C 570 390, 690 420, 760 455" fill="none" stroke="var(--ink)" stroke-width="3"/>
  </svg>

  <div class="brand-front">
    <div class="brand-row">
      <span class="brand-mark"></span>
      <span class="brand-name">Ridgeway<br>Systems</span>
    </div>
    <p class="tagline">Complete IT Management</p>
  </div>

  <span class="divider"></span>

  <div class="person">
    <p class="person-name">Daniel Reeves</p>
    <p class="person-role">Operation Manager</p>
    <ul class="contacts">
      <li><svg viewBox="0 0 16 16"><path d="M3 1l3 3-1.5 2a9 9 0 0 0 5.5 5.5L12 10l3 3-2 2C7 15 1 9 1 3z"/></svg>08 9362 4815</li>
      <li><svg viewBox="0 0 16 16"><path d="M4 0h8a1 1 0 0 1 1 1v14a1 1 0 0 1-1 1H4a1 1 0 0 1-1-1V1a1 1 0 0 1 1-1zm1 2v9h6V2zm3 10.5a1 1 0 1 0 0 2 1 1 0 0 0 0-2z"/></svg>0412 708 936</li>
      <li><svg viewBox="0 0 16 16"><path d="M4 1h7l2 2v3H4zM1 7h14v6h-2v2H3v-2H1zm4 4v3h6v-3z"/></svg>08 9362 4815</li>
      <li><svg viewBox="0 0 16 16"><path d="M1 3h14v10H1zm1.5 1.5L8 9l5.5-4.5z"/></svg>daniel@ridgewaysystems.com.au</li>
      <li><svg viewBox="0 0 16 16"><path d="M8 1a7 7 0 1 0 0 14A7 7 0 0 0 8 1zm0 1.5c.8 1 1.4 2.5 1.6 4H6.4C6.6 5 7.2 3.5 8 2.5zM2.6 7.5h2.3c.1 1.5.5 2.9 1.1 4a5.5 5.5 0 0 1-3.4-4zm0-1A5.5 5.5 0 0 1 6 3c-.6 1.1-1 2.5-1.1 3.5zm3.8 1h3.2c-.2 1.5-.8 3-1.6 4-.8-1-1.4-2.5-1.6-4zm4.7 0h2.3a5.5 5.5 0 0 1-3.4 4c.6-1.1 1-2.5 1.1-4zm0-1c-.1-1-.5-2.4-1.1-3.5a5.5 5.5 0 0 1 3.4 3.5z"/></svg>www.ridgewaysystems.com.au</li>
    </ul>
  </div>

  <address class="address" style="font-style:normal">
    Unit 4 18 Harbourview Road<br>Bibra Lake WA 6163
  </address>
</section>

</body>
</html>
```